Bulldog themed background for Real Estate Purchase Letter

I need a phantom background or watermark on a standard 8 1/2" x 11" paper. I am going to put a letter over the background. I want a bulldog theme that is cute, funny and original. This letter is for a real estate project and we want to capture the person sub-consciously . Attached is my personal dogs. If you want to use them you can but not required. I have attached the letter that I am trying to emulate. I want bulldogs not horses.

Target Market(s)

45 years old and higher

Industry/Entity Type

Real Estate

Font styles to use
Serif
Sans Serif

Colors

Designer to choose colors to be used in the design.

Requirements
Must have
• fun, happiness, reassuring,
Should not have
• violence, negativity, unhappy

```html
<!DOCTYPE html>
<html lang="en">
<head>
<meta charset="utf-8">
<title>Purchase Letter – Bulldog Letterhead</title>
<link href="https://fonts.googleapis.com/css2?family=Roboto:wght@400&family=Questrial&family=Crimson+Text:wght@400&display=swap" rel="stylesheet">
<style>
  :root {
    --backdrop: #e6e6e6;
    --paper: #ffffff;
    --ink: #2b2b2b;
    --ink-soft: #555555;
    --swoosh: #000000;
    --swoosh-edge: #cfcfcf;
    --signature-blue: #1f4f9c;
    --photo-light: #f1efed;
    --photo-mid: #cfc9c3;
    --photo-deep: #b9afa6;
  }
  * { margin: 0; padding: 0; box-sizing: border-box; }
  html, body { width: 1024px; height: 1200px; overflow: hidden; background: var(--backdrop); }
  .letter {
    position: absolute; left: 97px; top: 20px;
    width: 829px; height: 1160px;
    background: var(--paper);
    overflow: hidden;
    color: var(--ink);
  }
  .letter__photo {
    position: absolute; inset: 0;
    background:
      radial-gradient(ellipse 50% 38% at 55% 45%, var(--photo-deep) 0%, transparent 70%),
      radial-gradient(ellipse 70% 45% at 55% 78%, var(--photo-light) 0%, transparent 75%),
      linear-gradient(180deg, var(--photo-mid) 0%, var(--photo-light) 40%, var(--photo-light) 100%);
    opacity: .55;
  }
  .letter__swooshes { position: absolute; inset: 0; width: 100%; height: 100%; }
  .block { position: absolute; left: 88px; width: 661px; }
  .recipient__name { position: absolute; left: 88px; top: 127px; font: 400 17px/20px "Roboto", sans-serif; }
  .recipient__address { position: absolute; left: 88px; top: 171px; font: 400 17px/22px "Roboto", sans-serif; }
  .agent-title { position: absolute; top: 147px; right: 80px; font: 400 16px/20px "Roboto", sans-serif; }
  .salutation { top: 272px; font: 400 14.5px/20px "Questrial", sans-serif; }
  .body-text { font: 400 14px/26px "Questrial", sans-serif; letter-spacing: .25px; text-align: justify; color: var(--ink-soft); }
  .para-1 { top: 321px; }
  .para-2 { top: 452px; }
  .para-3 { top: 609px; }
  .body-text strong { color: var(--ink); }
  .closing { top: 795px; font: 400 14.5px/20px "Questrial", sans-serif; color: var(--ink-soft); }
  .signature-mark { position: absolute; left: 88px; top: 832px; width: 110px; height: 40px; }
  .signer { top: 890px; font: 400 23px/30px "Crimson Text", serif; color: var(--signature-blue); }
  .signer-phone { top: 926px; font: 400 16px/20px "Roboto", sans-serif; color: var(--ink-soft); }
  .postscript { top: 1003px; font: 400 16px/26px "Roboto", sans-serif; width: 530px; }
</style>
</head>
<body>
  <main class="letter">
    <div class="letter__photo" role="img" aria-label="Faint full-page photo of a smiling white bulldog as a watermark background"></div>

    <svg class="letter__swooshes" viewBox="0 0 667 933" preserveAspectRatio="none" aria-hidden="true">
      <path d="M0 0 H238 C130 22 40 62 0 122 Z" fill="var(--swoosh)"/>
      <path d="M238 0 C130 24 40 66 0 122 L0 112 C40 56 125 18 220 0 Z" fill="var(--swoosh-edge)"/>
      <path d="M667 933 H363 C490 905 630 860 667 772 Z" fill="var(--swoosh)"/>
      <path d="M363 933 C490 905 630 860 667 772 L667 786 C628 872 500 914 385 933 Z" fill="var(--swoosh-edge)"/>
    </svg>

    <p class="recipient__name">Mr Outta State Owner</p>
    <p class="recipient__address">2210 Lakeview Drive,<br>BROOKDALE FL 30000</p>
    <p class="agent-title">Licensed Real estate agent</p>

    <p class="block salutation">Dear Home Owner</p>

    <p class="block body-text para-1">I am writing you because I am interested in purchasing your property located at <strong>48 NE Harbor Ave BROOKDALE FL.</strong> I live nearby in Cedar Hollow and I Purchase properties throughout the state of Flordia. Currently I am working on projects in the neighborhood, which is how I learned of your property.</p>

    <p class="block body-text para-2">Please call me at . So i can tell you how we can buy your property quickly, with no hassles and most importantly, at a fair price. I purchase the house directly from you, so there are no real estate commissions or extr fees coming out of your pocket. Furthermore, I always make cash offers so you never have to worry about delays resulting from a buyer trying to quality for a morgage and wastingyour valuble time.</p>

    <p class="block body-text para-3">I'll be glad to personally tell you more about how we can work together. All calls are completely confidential and there is no obligation whatsoever. Even if you are not inteested in selling at this time call (555) 555-0142. So i can help you with derermining the value of your property. You should also keep this letter for further reference. since things in life have a tendency to chagne unexpectedly. Thank you for your time and consideration and I look forward to speaking with you.</p>

    <p class="block closing">Sincerely,</p>
    <svg class="signature-mark" viewBox="0 0 110 40" aria-hidden="true">
      <path d="M2 22 C30 16 50 8 60 12 C68 16 60 26 52 22 C62 16 82 24 106 24" fill="none" stroke="var(--signature-blue)" stroke-width="2" stroke-linecap="round"/>
    </svg>
    <p class="block signer">Dana Whitfield</p>
    <p class="block signer-phone">(555) 555-0142</p>

    <p class="block postscript">P.S. If you would like to e-mail me information and pictures of your property. please send them to DANAW@homeletter.com</p>
  </main>
</body>
</html>
```